Business Card Design Project

This is the first time we use our new logo. We need a business card that we can use both on our institutional corporate relationships and also that works for our staff that deals with consumers directly.

VELUNDA is a new company dedicated to empower consumers and to provide them with the best choices for specialized health care using the latest telemedicine technology (medicine at a distance via videoconference).

We want to print this cards in high quality materials and process. We will like designs that allow us to use UV spot varnish and other techniques that will differentiate us.

We are including Two different versions of Color logos. In addition we are including white over black background logos. Those can be used replacing the black for a color.

Please note this is the first time we will be creating any corporate materials with our new logo and colors.

Target Market(s)

34+ consumers of medium high and high socioeconomic levels.

Industry/Entity Type

Health

Requirements
Must have
• Our logo on its original colors
Should not have
• Any other graphical element or design that is not our logo

```html
<!DOCTYPE html>
<html lang="en">
<head>
<meta charset="utf-8">
<title>VELUNDA Business Card</title>
<link rel="stylesheet" href="https://fonts.googleapis.com/css2?family=Arimo:wght@400;700&display=swap">
<style>
  :root {
    --backdrop: #e7e4e0;
    --card-black: #0b0b0c;
    --texture-dark: #1c1c1e;
    --texture-light: #2a2a2d;
    --rule: #8a97a8;
    --brand-blue: #a9c4e4;
    --label-blue: #9fb4cf;
    --name-white: #e8e8e8;
    --logo-white: #ffffff;
  }
  * { box-sizing: border-box; margin: 0; padding: 0; }
  html, body {
    width: 1200px;
    height: 750px;
    overflow: hidden;
  }
  body {
    background: var(--backdrop);
    font-family: "Arimo", Arial, sans-serif;
    position: relative;
  }
  .card {
    position: absolute;
    left: 310px;
    width: 580px;
    height: 320px;
    border-radius: 22px;
    overflow: hidden;
    background: var(--card-black);
    box-shadow: 0 6px 16px rgba(0,0,0,0.35);
  }
  .card--front { top: 18px; }
  .card--back { top: 381px; }

  .texture {
    position: absolute;
    left: 0;
    right: 0;
    background: linear-gradient(135deg, var(--texture-light), var(--texture-dark));
  }
  .band {
    position: absolute;
    left: 0;
    right: 0;
    background: var(--card-black);
    border-top: 1px solid var(--rule);
    border-bottom: 1px solid var(--rule);
  }

  /* Front */
  .card--front .texture--top { top: 0; height: 86px; }
  .card--front .texture--bottom { top: 235px; bottom: 0; }
  .card--front .band { top: 86px; height: 149px; }
  .front-brand {
    position: absolute;
    left: 36px;
    top: 0;
    height: 100%;
    display: flex;
    align-items: center;
    gap: 92px;
  }
  .brand-dot {
    width: 58px;
    height: 58px;
    border-radius: 50%;
    background: var(--brand-blue);
  }
  .front-brand__name {
    font-size: 58px;
    font-weight: 700;
    letter-spacing: 3px;
    color: var(--brand-blue);
    margin-top: 24px;
  }

  /* Back */
  .card--back .texture--top { top: 0; height: 84px; }
  .card--back .texture--bottom { top: 232px; bottom: 0; }
  .card--back .band { top: 84px; height: 148px; }
  .holder {
    position: absolute;
    left: 23px;
    top: 24px;
    width: 255px;
    text-align: right;
  }
  .holder__name {
    font-size: 33px;
    font-weight: 700;
    color: var(--name-white);
    text-align: left;
    white-space: nowrap;
  }
  .holder__title {
    font-size: 19px;
    color: var(--label-blue);
    margin-top: 2px;
  }
  .back-brand {
    position: absolute;
    left: 335px;
    top: 26px;
    width: 180px;
    display: flex;
    flex-direction: column;
    align-items: center;
    gap: 16px;
  }
  .back-brand .brand-dot {
    width: 44px;
    height: 44px;
    background: var(--logo-white);
  }
  .back-brand__name {
    font-size: 26px;
    font-weight: 700;
    letter-spacing: 1.5px;
    color: var(--logo-white);
  }
  .contact {
    position: absolute;
    top: 241px;
    font-size: 19px;
    font-weight: 700;
    line-height: 20px;
    color: var(--label-blue);
    list-style: none;
  }
  .contact--left { left: 25px; }
  .contact--right { left: 326px; }
</style>
</head>
<body>
  <section class="card card--front">
    <div class="texture texture--top" role="img" aria-label="Dark diagonal carbon-stripe texture"></div>
    <div class="band">
      <div class="front-brand">
        <span class="brand-dot"></span>
        <span class="front-brand__name">VELUNDA</span>
      </div>
    </div>
    <div class="texture texture--bottom" role="img" aria-label="Dark diagonal carbon-stripe texture"></div>
  </section>

  <section class="card card--back">
    <div class="texture texture--top" role="img" aria-label="Dark diagonal carbon-stripe texture"></div>
    <div class="band">
      <div class="holder">
        <p class="holder__name">Name Surname</p>
        <p class="holder__title">TITLE</p>
      </div>
      <div class="back-brand">
        <span class="brand-dot"></span>
        <span class="back-brand__name">VELUNDA</span>
      </div>
    </div>
    <div class="texture texture--bottom" role="img" aria-label="Dark diagonal carbon-stripe texture"></div>
    <ul class="contact contact--left">
      <li>Adress:</li>
      <li>Cell:</li>
      <li>Email:</li>
    </ul>
    <ul class="contact contact--right">
      <li>Phone:</li>
      <li>Fax:</li>
    </ul>
  </section>
</body>
</html>
```